Card Design for my dog training business Brightpaw Obedience

Need a business card design for my dog training business with my new logo. Want the card to come off professional yet fun. Want it to be very eye catchy as well. I normally have these at vet clinics, pet stores, and groomers. so need it to look better than my competitors.
Target Market(s)
dog owners
Industry/Entity Type
Dog Training
Contact Information for Business Card
needs logo, my name and info
Font styles to use
Serif
Colors
0255a3
ffffff
ec1f27
000000
333333
fbfbfb
Requirements
Must have
- Brightpaw Obedience
- Felix Orland
- 415 903 2276
- info@brightpawobedience.example
- www.brightpawobedience.example

```html
<!DOCTYPE html>
<html lang="en">
<head>
<meta charset="utf-8">
<title>Brightpaw Obedience — Business Card</title>
<link rel="stylesheet" href="https://fonts.googleapis.com/css2?family=EB+Garamond:ital@1&family=Merriweather:wght@300;400&display=swap">
<style>
  :root {
    --brand-blue: #0255a3;
    --brand-blue-deep: #024a8e;
    --brand-red: #ec1f27;
    --ink-black: #000000;
    --ink-dark: #333333;
    --paper: #fbfbfb;
    --white: #ffffff;
    --backdrop: #b4b4b4;
  }
  * { box-sizing: border-box; margin: 0; padding: 0; }
  html, body {
    width: 1200px; height: 576px; overflow: hidden;
    background: var(--backdrop);
  }
  .canvas { position: relative; width: 1200px; height: 576px; }

  .card {
    position: absolute; top: 138px;
    width: 484px; height: 294px;
    border-radius: 12px; overflow: hidden;
    box-shadow: 0 3px 6px rgba(0,0,0,0.25);
  }

  /* Front */
  .card-front {
    left: 82px;
    background: linear-gradient(180deg, var(--brand-blue-deep) 0%, var(--brand-blue) 100%);
  }
  .front-brand {
    position: absolute; left: 0; right: 0; top: 103px;
    text-align: center;
    font-family: "Merriweather", Georgia, serif; font-weight: 400;
    font-size: 26px; letter-spacing: 0.5px;
    color: var(--white);
  }
  .tagline-band {
    position: absolute; left: 0; right: 0; top: 255px; height: 28px;
    background: var(--ink-black);
    display: flex; align-items: center; justify-content: center;
  }
  .tagline {
    font-family: "EB Garamond", Georgia, serif; font-style: italic;
    font-size: 12px; color: var(--white); white-space: nowrap;
  }

  /* Back */
  .card-back {
    left: 602px; height: 292px;
    background: linear-gradient(180deg, var(--paper) 0%, #ececec 100%);
  }
  .back-brand {
    position: absolute; left: 24px; top: 88px;
    font-family: "Merriweather", Georgia, serif; font-weight: 400;
    font-size: 19px; color: var(--brand-blue);
  }
  .person {
    position: absolute; right: 24px; top: 148px; text-align: right;
    font-family: "Merriweather", Georgia, serif;
  }
  .person-name { font-size: 18px; font-weight: 400; color: var(--brand-blue); line-height: 1.3; }
  .person-role { font-size: 11px; font-weight: 300; color: var(--ink-dark); margin-top: 3px; }
  .divider {
    position: absolute; left: 24px; right: 24px; top: 204px;
    height: 1.5px; background: var(--brand-red);
  }
  .contact-list {
    position: absolute; left: 28px; top: 217px; list-style: none;
    font-family: "Merriweather", Georgia, serif; font-weight: 300;
    font-size: 11.5px; color: var(--ink-dark);
  }
  .contact-item { display: flex; align-items: center; height: 19px; white-space: nowrap; }
  .contact-icon { width: 11px; height: 11px; margin-right: 9px; flex: none; }
</style>
</head>
<body>
<main class="canvas">
  <section class="card card-front" aria-label="Card front">
    <div class="front-brand">Brightpaw Obedience</div>
    <div class="tagline-band">
      <p class="tagline">“Patient lessons for happy dogs and their people.”</p>
    </div>
  </section>

  <section class="card card-back" aria-label="Card back">
    <div class="back-brand">Brightpaw Obedience</div>
    <div class="person">
      <div class="person-name">Felix Orland</div>
      <div class="person-role">Dog Trainer</div>
    </div>
    <div class="divider"></div>
    <ul class="contact-list">
      <li class="contact-item">
        <svg class="contact-icon" viewBox="0 0 12 12" aria-hidden="true">
          <path d="M1 4 Q6 0 11 4 L9.5 5.2 L8 4 L4 4 L2.5 5.2 Z" fill="#0255a3"/>
          <rect x="2.5" y="5.5" width="7" height="5" rx="0.8" fill="#0255a3"/>
        </svg>
        415 903 2276
      </li>
      <li class="contact-item">
        <svg class="contact-icon" viewBox="0 0 12 12" aria-hidden="true">
          <rect x="0.5" y="2" width="11" height="8" fill="#0255a3"/>
          <path d="M0.8 2.4 L6 6.6 L11.2 2.4" fill="none" stroke="#fbfbfb" stroke-width="1"/>
        </svg>
        info@brightpawobedience.example
      </li>
      <li class="contact-item">
        <svg class="contact-icon" viewBox="0 0 12 12" aria-hidden="true">
          <circle cx="6" cy="6" r="5" fill="#0255a3"/>
          <path d="M1 6 H11 M6 1 V11 M6 1 Q2.5 6 6 11 M6 1 Q9.5 6 6 11" fill="none" stroke="#fbfbfb" stroke-width="0.7"/>
        </svg>
        www.brightpawobedience.example
      </li>
    </ul>
  </section>
</main>
</body>
</html>
```